Gobal construction supply company needs new business card design

I need a business card design for my global supply company using an existing logo. i will be looking to print these on rounded corner cards with the black background version of my logo on the back. on the front white background, my logo again and my simple details.

```html
<!DOCTYPE html>
<html lang="en">
<head>
<meta charset="utf-8">
<title>Meridian Supply Group – Business Card</title>
<link href="https://fonts.googleapis.com/css2?family=Montserrat:wght@400;600;700&family=Inter:wght@400;500&display=swap" rel="stylesheet">
<style>
  :root {
    --backdrop: #2b2a2b;
    --card-dark: #1f1d1f;
    --card-dark-soft: #2c2a2c;
    --brand-red: #d71f26;
    --swoosh-grey: #444444;
    --ink: #1c1c1c;
    --paper: #ffffff;
    --muted: #333333;
  }
  * { box-sizing: border-box; margin: 0; padding: 0; }
  html, body { width: 1200px; height: 930px; overflow: hidden; }
  body {
    background: var(--backdrop);
    font-family: "Inter", sans-serif;
    position: relative;
  }
  .card {
    position: absolute;
    width: 700px;
    height: 400px;
    border-radius: 22px;
    overflow: hidden;
  }

  /* Back side */
  .card-back {
    left: 60px; top: 45px;
    background: linear-gradient(160deg, var(--card-dark-soft), var(--card-dark));
  }
  .card-back .world-map {
    position: absolute;
    left: 80px; top: 60px; width: 540px; height: 280px;
    background: radial-gradient(ellipse at center, rgba(255,255,255,0.07), rgba(255,255,255,0) 70%);
  }
  .card-back .brand {
    position: absolute;
    left: 0; right: 0; top: 165px;
    text-align: center;
  }
  .brand-name {
    font-family: "Montserrat", sans-serif;
    font-weight: 700;
    font-size: 34px;
    letter-spacing: 1px;
    display: inline-flex;
    align-items: center;
    gap: 14px;
    white-space: nowrap;
  }
  .brand-mark { width: 22px; height: 22px; background: var(--brand-red); display: inline-block; }
  .card-back .brand-name { color: var(--paper); }
  .brand-rule {
    width: 420px; height: 2px; background: var(--brand-red);
    margin: 18px auto 0;
  }

  /* Front side */
  .card-front {
    left: 440px; top: 490px;
    background: var(--paper);
  }
  .card-front .swoosh { position: absolute; left: 0; top: 0; }
  .card-front .brand {
    position: absolute; left: 40px; top: 200px;
  }
  .card-front .brand-name { font-size: 22px; color: var(--ink); gap: 10px; }
  .card-front .brand-mark { width: 16px; height: 16px; }
  .card-front .brand-rule { width: 300px; margin: 10px 0 0; }
  .person {
    position: absolute; right: 40px; top: 145px; text-align: right;
  }
  .person-name {
    font-family: "Montserrat", sans-serif;
    font-weight: 600; font-size: 28px; color: var(--brand-red);
    white-space: nowrap;
  }
  .person-title { font-size: 17px; color: var(--ink); margin-top: 2px; }
  .divider {
    position: absolute; left: 40px; right: 40px; top: 262px;
    height: 2px; background: var(--brand-red);
  }
  .contact-list {
    position: absolute; left: 40px; top: 285px;
    list-style: none; font-size: 17px; color: var(--muted); line-height: 1.55;
  }
  .contact-list li { display: flex; align-items: center; gap: 10px; }
  .contact-list svg { width: 13px; height: 13px; flex: none; }
  .contact-list .accent { color: var(--brand-red); }
  .address {
    position: absolute; right: 40px; top: 290px; text-align: right;
    font-size: 17px; color: var(--muted); line-height: 1.5; font-style: normal;
  }
</style>
</head>
<body>

<section class="card card-back" aria-label="Card back">
  <div class="world-map" role="img" aria-label="Faint dotted world map"></div>
  <div class="brand">
    <div class="brand-name"><span class="brand-mark"></span>MERIDIAN SUPPLY GROUP</div>
    <div class="brand-rule"></div>
  </div>
</section>

<section class="card card-front" aria-label="Card front">
  <svg class="swoosh" width="700" height="400" viewBox="0 0 700 400" aria-hidden="true">
    <path d="M0 0 H700 V30 C600 88 420 95 280 100 C150 105 50 130 0 165 Z" fill="var(--card-dark)"/>
    <path d="M0 165 C50 130 150 105 280 100 C420 95 600 88 700 30 V55 C600 108 420 116 280 120 C160 124 60 145 0 188 Z" fill="var(--brand-red)"/>
    <path d="M0 188 C60 145 160 124 260 121 C170 132 80 158 25 200 L0 212 Z" fill="var(--swoosh-grey)"/>
  </svg>

  <div class="brand">
    <div class="brand-name"><span class="brand-mark"></span>MERIDIAN SUPPLY GROUP</div>
    <div class="brand-rule"></div>
  </div>

  <div class="person">
    <div class="person-name">DANIEL HART</div>
    <div class="person-title">Director</div>
  </div>

  <div class="divider"></div>

  <ul class="contact-list">
    <li>
      <svg viewBox="0 0 16 16" aria-hidden="true"><path d="M3 1l3 3-2 2c1 2 3 4 5 5l2-2 3 3-2 3C7 15 1 9 1 3z" fill="var(--brand-red)"/></svg>
      403-555-0182
    </li>
    <li>
      <svg viewBox="0 0 16 16" aria-hidden="true"><rect x="1" y="3" width="14" height="10" fill="none" stroke="var(--brand-red)" stroke-width="1.6"/><path d="M1 3l7 6 7-6" fill="none" stroke="var(--brand-red)" stroke-width="1.6"/></svg>
      info@meridiansupply.com
    </li>
    <li>
      <svg viewBox="0 0 16 16" aria-hidden="true"><circle cx="8" cy="8" r="6.5" fill="none" stroke="var(--brand-red)" stroke-width="1.4"/><path d="M1.5 8h13M8 1.5c-3 3.5-3 9.5 0 13M8 1.5c3 3.5 3 9.5 0 13" fill="none" stroke="var(--brand-red)" stroke-width="1.2"/></svg>
      <span>www.<span class="accent">meridiansupply</span>.com</span>
    </li>
  </ul>

  <address class="address">
    48 Quarry Road Box<br>2210, Red Deer, AB
  </address>
</section>

</body>
</html>
```